Storm Restoration Contractor needs a professional letterhead design

Looking for a professional letterhead design. Not looking for your cheapo MS Word standard ones that are readily available. Dont want it to be cookie cutter look like ones readily available online. We just recently changed our logo and want to freshen up all our documents. Our company handles restoring a property back to a pre-loss condition after a storm damages it. For example, wind, hail, flood, fire losses.

Target Market(s)

Property Owners, Homeowners, Property Owners, Commercial Property Owners, Property Management Companies

Industry/Entity Type

Construction Company

Requirements
Must have
• Professional, Use 1 of 2 logo options
• Storm Restoration, Roofing, Siding, Windows

```html
<!DOCTYPE html>
<html lang="en">
<head>
<meta charset="utf-8">
<title>Stormline Builders Letterhead</title>
<link href="https://fonts.googleapis.com/css2?family=Questrial&display=swap" rel="stylesheet">
<style>
  :root {
    --backdrop: #bdbdbd;
    --paper: #f2f2f2;
    --brand-blue: #2266b0;
    --ink: #444444;
    --rule: #b9b9b9;
    --watermark: #e9e9e9;
  }
  * { margin: 0; padding: 0; box-sizing: border-box; }
  html, body {
    width: 1200px; height: 1041px; overflow: hidden;
    background: var(--backdrop);
    font-family: "Questrial", "Century Gothic", sans-serif;
  }
  .letterhead {
    position: absolute; left: 198px; top: 0;
    width: 804px; height: 1041px;
    background: var(--paper);
  }
  .brand {
    position: absolute; left: 274px; top: 54px;
    display: flex; align-items: center; gap: 10px;
  }
  .brand-dot {
    width: 62px; height: 62px; border-radius: 50%;
    border: 7px solid var(--brand-blue);
  }
  .brand-divider {
    width: 2px; height: 66px; background: var(--brand-blue);
  }
  .brand-name {
    color: var(--brand-blue);
    font-size: 26px; line-height: 25px; letter-spacing: 1.5px;
    text-transform: uppercase;
  }
  .watermark-ring {
    position: absolute; left: 152px; top: 269px;
    width: 496px; height: 496px; border-radius: 50%;
    border: 38px solid var(--watermark);
  }
  .contact-bar {
    position: absolute; left: 0; top: 924px; width: 100%;
    font-size: 11px; color: var(--ink); text-align: center; line-height: 14px;
  }
  .contact-item {
    position: absolute; top: 0;
    display: flex; flex-direction: column; align-items: center;
    transform: translateX(-50%); white-space: nowrap;
  }
  .contact-item svg { width: 28px; height: 28px; margin-bottom: 8px; }
  .contact-divider {
    position: absolute; top: 3px; width: 1px; height: 66px; background: var(--rule);
  }
  .footer-band {
    position: absolute; left: 0; top: 1022px; width: 100%; height: 14px;
    background: var(--brand-blue);
  }
</style>
</head>
<body>
  <main class="letterhead">
    <header class="brand">
      <div class="brand-dot"></div>
      <div class="brand-divider"></div>
      <div class="brand-name">Stormline<br>Builders</div>
    </header>

    <div class="watermark-ring" aria-hidden="true"></div>

    <footer class="contact-bar">
      <div class="contact-item" style="left:158px">
        <svg viewBox="0 0 28 28" aria-hidden="true">
          <circle cx="14" cy="14" r="14" fill="var(--brand-blue)"/>
          <path d="M14 6a5.5 5.5 0 0 0-5.5 5.5C8.5 16 14 22 14 22s5.5-6 5.5-10.5A5.5 5.5 0 0 0 14 6z" fill="#fff"/>
          <circle cx="14" cy="11.5" r="2.2" fill="var(--brand-blue)"/>
        </svg>
        <span>4210 E Canyon Ridge Road STE 204<br>Mesa, AZ 85215</span>
      </div>
      <div class="contact-divider" style="left:264px"></div>
      <div class="contact-item" style="left:330px">
        <svg viewBox="0 0 28 28" aria-hidden="true">
          <circle cx="14" cy="14" r="14" fill="var(--brand-blue)"/>
          <path d="M10 7.5l2.5-.5 1.5 3.5-1.8 1.3c.8 1.8 2.2 3.2 4 4l1.3-1.8 3.5 1.5-.5 2.5c-.3 1-1.3 1.6-2.3 1.4C12.5 18.4 9.6 15.5 8.6 9.8 8.4 8.8 9 7.8 10 7.5z" fill="#fff"/>
        </svg>
        <span>555-014-2870</span>
      </div>
      <div class="contact-divider" style="left:396px"></div>
      <div class="contact-item" style="left:483px">
        <svg viewBox="0 0 28 28" aria-hidden="true">
          <circle cx="14" cy="14" r="14" fill="var(--brand-blue)"/>
          <rect x="7" y="9" width="14" height="10" fill="#fff"/>
          <path d="M7 9l7 5.5L21 9M7 19l5-5M21 19l-5-5" fill="none" stroke="var(--brand-blue)" stroke-width="1.2"/>
        </svg>
        <span>info@stormlinebuilders.com</span>
      </div>
      <div class="contact-divider" style="left:570px"></div>
      <div class="contact-item" style="left:659px">
        <svg viewBox="0 0 28 28" aria-hidden="true">
          <circle cx="14" cy="14" r="14" fill="var(--brand-blue)"/>
          <g fill="none" stroke="#fff" stroke-width="1.3">
            <circle cx="14" cy="14" r="8"/>
            <ellipse cx="14" cy="14" rx="3.5" ry="8"/>
            <path d="M6 14h16M7.2 10h13.6M7.2 18h13.6"/>
          </g>
        </svg>
        <span>www.stormlinebuilders.com</span>
      </div>
    </footer>

    <div class="footer-band"></div>
  </main>
</body>
</html>
```